New Business Card for Web Design/Internet Marketing Company

Looking for a great looking new business card. We are a 10 year old web design, internet marketing and website management company that works mostly with small businesses.

Our new card needs to better match the colors and style of our website, be bold, extremely usable and slightly edgy.

Target Market(s)

Small/Medium businesses that have websites

Industry/Entity Type

Internet

Requirements
Must have
• Front and back design, full color, rounded corners please

Must use the colors/style of our website (JPG provided)

INFO FOR CARDS (as readable as possible please)
Mark Lenner
President/CEO
mark@trelvanmedia.example
Phone: 520-381-7459
Toll Free: 866-381-7459
Address: 4315 W. Calloway Ave. Ste. 140, Tucson, AZ 85792

THINGS I WANT TO PROMOTE (if there is room):
1. Our Website - www.trelvanmedia.example

2. Social Media
Twitter: @trelvanmedia
Facebook: www.facebook.com/trelvanmedia

3. Our Services
Web Design
Internet Marketing
Website Management

```html
<!DOCTYPE html>
<html lang="en">
<head>
<meta charset="utf-8">
<title>Trelvan Media – Business Card</title>
<link rel="stylesheet" href="https://fonts.googleapis.com/css2?family=Source+Sans+3:wght@400;600;700&display=swap">
<style>
  :root {
    --navy: #233f70;
    --white: #ffffff;
    --grey: #6b6b6d;
    --orange: #f07f22;
    --blue: #1d9ad6;
    --backdrop: #e9e6e1;
    --soft-white: rgba(255,255,255,0.85);
  }
  html, body {
    margin: 0;
    padding: 0;
    overflow: hidden;
  }
  body {
    width: 1200px;
    height: 402px;
    background: var(--backdrop);
    position: relative;
    font-family: "Source Sans 3", sans-serif;
  }
  .card {
    position: absolute;
    top: 57px;
    width: 512px;
    height: 292px;
    border-radius: 14px;
    overflow: hidden;
  }
  .card--front { left: 63px; background: var(--white); }
  .card--back { left: 627px; background: var(--navy); }

  .front-band {
    position: absolute;
    left: 0; top: 0;
    width: 512px; height: 292px;
  }
  .brand {
    position: absolute;
    left: 0; right: 0;
    top: 48px;
    display: flex;
    align-items: center;
    justify-content: center;
    gap: 12px;
  }
  .brand__dot {
    width: 28px; height: 28px;
    border-radius: 50%;
    background: var(--blue);
  }
  .brand__name {
    font-weight: 700;
    font-size: 46px;
    line-height: 1;
    color: var(--orange);
    letter-spacing: -0.5px;
  }
  .tagline {
    position: absolute;
    right: 34px;
    top: 104px;
    font-size: 16px;
    color: var(--grey);
  }
  .contact {
    position: absolute;
    right: 222px;
    top: 187px;
    margin: 0;
    padding: 0;
    list-style: none;
    color: var(--white);
    font-size: 12.5px;
    line-height: 15.5px;
    text-align: right;
  }
  .contact li { display: flex; justify-content: flex-end; align-items: center; gap: 5px; }
  .contact .icon { width: 9px; height: 9px; fill: var(--white); flex: none; }
  .contact .address { display: block; padding-right: 14px; }
  .divider {
    position: absolute;
    left: 320px; top: 190px;
    width: 1px; height: 96px;
    background: var(--white);
  }
  .person {
    position: absolute;
    left: 330px; width: 140px;
    top: 224px;
    text-align: center;
    color: var(--white);
  }
  .person__name { font-weight: 700; font-size: 17px; line-height: 1.1; }
  .person__role { font-size: 12.5px; }

  .social {
    position: absolute;
    left: 290px; top: 40px;
    margin: 0; padding: 0;
    list-style: none;
    color: var(--white);
    font-size: 17px;
    line-height: 24px;
  }
  .social li { display: flex; align-items: center; gap: 9px; }
  .social__mark {
    width: 16px; height: 16px;
    border-radius: 2px;
    background: var(--soft-white);
  }
  .back-name {
    position: absolute;
    left: 26px; top: 162px;
    display: flex; align-items: center; gap: 9px;
    font-weight: 700;
    font-size: 30px;
    line-height: 1;
    color: var(--white);
  }
  .back-name__dot {
    width: 16px; height: 16px;
    border-radius: 50%;
    background: var(--white);
  }
  .services {
    position: absolute;
    left: 289px; top: 164px;
    margin: 0; padding: 0;
    list-style: none;
    color: var(--white);
    font-size: 22px;
    line-height: 31px;
  }
</style>
</head>
<body>
  <section class="card card--front" aria-label="Card front">
    <svg class="front-band" viewBox="0 0 512 292" aria-hidden="true">
      <path d="M0 146 Q256 166 512 140 L512 292 L0 292 Z" fill="var(--grey)"/>
      <path d="M0 158 Q200 174 392 166 L400 182 L410 164 Q470 160 512 152 L512 292 L0 292 Z" fill="var(--navy)"/>
    </svg>

    <div class="brand">
      <span class="brand__dot"></span>
      <span class="brand__name">Trelvan Media</span>
    </div>
    <div class="tagline">Grow your Website</div>

    <ul class="contact">
      <li>520-381-7459 <svg class="icon" viewBox="0 0 10 10"><circle cx="5" cy="5" r="5"/></svg></li>
      <li>866-381-7459 <svg class="icon" viewBox="0 0 10 10"><path d="M2 1 L4 1 L5 3 L4 4 Q5 6 6 6 L7 5 L9 6 L9 8 Q8 9 7 9 Q1 8 1 2 Q1 1 2 1 Z"/></svg></li>
      <li>mark@trelvanmedia.example <svg class="icon" viewBox="0 0 10 10"><rect x="0" y="2" width="10" height="6"/></svg></li>
      <li>www.trelvanmedia.example <svg class="icon" viewBox="0 0 10 10"><circle cx="5" cy="5" r="4.5" fill="none" stroke="#fff" stroke-width="1.2"/><line x1="0.5" y1="5" x2="9.5" y2="5" stroke="#fff" stroke-width="1"/><ellipse cx="5" cy="5" rx="2" ry="4.5" fill="none" stroke="#fff" stroke-width="1"/></svg></li>
      <li class="address">4315 W. Calloway Ave., Ste. 140<br>Tucson, AZ 85792</li>
    </ul>

    <div class="divider"></div>
    <div class="person">
      <div class="person__name">Mark Lenner</div>
      <div class="person__role">President/CEO</div>
    </div>
  </section>

  <section class="card card--back" aria-label="Card back">
    <ul class="social">
      <li><span class="social__mark"></span>@trelvanmedia</li>
      <li><span class="social__mark"></span>trelvanmedia</li>
    </ul>
    <div class="back-name">
      <span class="back-name__dot"></span>
      <span>Trelvan Media</span>
    </div>
    <ul class="services">
      <li>Web Design</li>
      <li>Internet Marketing</li>
      <li>Website Management</li>
    </ul>
  </section>
</body>
</html>
```